Oil and Gas Exploration and Production company needs a business card design

We need a business card design using our logo and colors in the logo. We want a mainstream design.

```html
<!DOCTYPE html>
<html lang="en">
<head>
<meta charset="utf-8">
<title>Solano Energy – Business Card</title>
<link href="https://fonts.googleapis.com/css2?family=Open+Sans:wght@400;700;800&display=swap" rel="stylesheet">
<style>
  :root {
    --backdrop: #2b2b2d;
    --paper: #fbfbfa;
    --ink: #231f20;
    --gold: #d4a02a;
    --grey: #6d6d6d;
  }
  html, body {
    margin: 0;
    padding: 0;
    overflow: hidden;
  }
  body {
    width: 1200px;
    height: 840px;
    background: var(--backdrop);
    font-family: "Open Sans", Arial, sans-serif;
    position: relative;
  }
  .card {
    position: absolute;
    left: 348px;
    width: 504px;
    height: 288px;
    background: var(--paper);
    box-sizing: border-box;
    overflow: hidden;
  }
  .card-back { top: 100px; }
  .card-front { top: 452px; }

  /* back side */
  .back-mark {
    position: absolute;
    left: 50%;
    top: 50%;
    transform: translate(-50%, -50%);
    display: flex;
    align-items: center;
    gap: 10px;
  }
  .mark-dot {
    width: 22px;
    height: 22px;
    border-radius: 50%;
    background: var(--gold);
  }
  .mark-name {
    font-weight: 800;
    color: var(--ink);
    font-size: 26px;
    letter-spacing: 0.5px;
  }
  .back-web {
    position: absolute;
    right: 14px;
    top: 50%;
    transform: translate(50%, -50%) rotate(-90deg);
    transform-origin: center;
    font-size: 9px;
    letter-spacing: 3px;
    color: var(--grey);
    white-space: nowrap;
    margin-right: 6px;
  }

  /* front side */
  .edge {
    position: absolute;
    top: 0;
    bottom: 0;
  }
  .edge-left-ink { left: 0; width: 4px; background: var(--ink); }
  .edge-left-gold { left: 7px; width: 4px; background: var(--gold); }
  .edge-right-gold { right: 7px; width: 4px; background: var(--gold); }

  .front-mark {
    position: absolute;
    left: 30px;
    top: 30px;
    display: flex;
    align-items: center;
    gap: 8px;
  }
  .front-mark .mark-dot { width: 18px; height: 18px; }
  .front-mark .mark-name { font-size: 30px; }

  .contact {
    position: absolute;
    left: 250px;
    top: 120px;
    color: var(--grey);
    font-size: 10.5px;
    line-height: 1.35;
  }
  .person-name {
    font-weight: 800;
    color: var(--ink);
    font-size: 14px;
    letter-spacing: 0.5px;
    margin: 0;
  }
  .person-title {
    color: var(--gold);
    font-size: 10.5px;
    letter-spacing: 0.5px;
    margin: 0 0 10px;
  }
  .address { margin: 0 0 10px; }
  .lines { margin: 0; padding: 0; list-style: none; }
  .lines b { color: var(--ink); font-weight: 700; }
</style>
</head>
<body>
  <section class="card card-back" aria-label="Business card, back">
    <div class="back-mark">
      <span class="mark-dot"></span>
      <span class="mark-name">Solano Energy</span>
    </div>
    <div class="back-web">www.solanoenergy.com</div>
  </section>

  <section class="card card-front" aria-label="Business card, front">
    <span class="edge edge-left-ink"></span>
    <span class="edge edge-left-gold"></span>
    <span class="edge edge-right-gold"></span>

    <div class="front-mark">
      <span class="mark-dot"></span>
      <span class="mark-name">Solano Energy</span>
    </div>

    <div class="contact">
      <p class="person-name">MARK ELLIS</p>
      <p class="person-title">PRESIDENT</p>
      <p class="address">2170 Harbor View Road<br>Lakeside, NY 10992</p>
      <ul class="lines">
        <li><b>Phone:</b> 555 0142 7710</li>
        <li><b>Mobile:</b> 555 0187 9024</li>
        <li><b>Fax:</b> 555 0163 4468</li>
        <li><b>Email:</b> info@solanoenergy.com</li>
      </ul>
    </div>
  </section>
</body>
</html>
```